NZ First of it's kind solutions directory and marketplace for busy Mums needs a business card design

We need a business card design for our new nationwide business in NZ (long term plans to go global). We provide solutions to the everyday challenges that busy Mums face by connecting them with quality communities and suppliers of carefully selected, relevant products and services. We sell direct via our online marketplace. The final design should communicate our values of inclusivity, quality and smart solutions. Colours should incorporate our logo colour palette of #477077 and #6ba8b2. Our website is at https://www.brightnestmums.example

Target Market(s)

busy Mums, Age 28 – 50, female, income over $100K, location main centres NZ primarily but NZ wide. Is likely juggling work or career with a young family. Probably had hobbies which have fallen by the wayside.
-Wants to succeed in her chosen career without compromising on family life
-to successfully juggle her career without feeling like she is compromising her children
- Is time poor, something always has to give and it’s generally her health (she’ll stay up late, get stressed)
- probably ex corporate or professional career. Has discretional income

Industry/Entity Type

Business

Contact Information for Business Card

Lena Forbisher, Founder, BrightNestMums.example (Strapline Tap; Gather; Sorted), 47 Kowhai Terrace, Ellerslie, Auckland 1051, New Zealand. Mob: 021 483 517 Ph: +64 (0)9 571 4860

Font styles to use
Other font styles liked:
• Raleway, and/or Architects Daughter

Colors
00a990
33b8a4
86cfc6
cfeae6

Requirements
Must have
• the above details, streamline. the logo and colours associated with those logos
Should not have
• foil or metallic colours

```html
<!DOCTYPE html>
<html lang="en">
<head>
<meta charset="utf-8">
<title>BrightNestMums – Business Card</title>
<link href="https://fonts.googleapis.com/css2?family=Roboto:ital,wght@0,400;0,500;1,400&display=swap" rel="stylesheet">
<style>
  :root {
    --page-bg: #d9d6d1;
    --card-bg: #eceeec;
    --brand-dark: #2f5a61;
    --brand-teal: #477077;
    --brand-light: #6ba8b2;
    --text-dark: #3a3f41;
    --name-cream: #e8dcc6;
  }
  * { box-sizing: border-box; margin: 0; padding: 0; }
  html, body {
    width: 1200px;
    height: 1047px;
    overflow: hidden;
    background: var(--page-bg);
    font-family: "Roboto", Arial, sans-serif;
  }
  .business-card {
    position: absolute;
    left: 100px;
    top: 223px;
    width: 1000px;
    height: 600px;
    background: var(--card-bg);
    border: 1px solid rgba(255,255,255,0.7);
    overflow: hidden;
  }
  .brand-name {
    position: absolute;
    left: 53px;
    top: 52px;
    font-size: 58px;
    font-weight: 500;
    letter-spacing: -0.5px;
    color: var(--brand-teal);
    line-height: 1;
  }
  .strapline {
    position: absolute;
    left: 55px;
    top: 142px;
    font-size: 20px;
    letter-spacing: 6px;
    color: var(--text-dark);
    text-transform: uppercase;
  }
  .strapline .divider { color: var(--brand-light); margin: 0 8px; }
  .address {
    position: absolute;
    left: 53px;
    top: 325px;
    font-size: 23px;
    line-height: 37px;
    color: var(--text-dark);
  }
  .contact-list {
    position: absolute;
    left: 53px;
    top: 420px;
    list-style: none;
    font-size: 23px;
    color: var(--text-dark);
  }
  .contact-list li {
    display: flex;
    align-items: center;
    height: 38px;
  }
  .contact-list svg {
    width: 20px;
    height: 20px;
    margin-right: 20px;
    fill: var(--brand-teal);
  }
  .brand-graphic {
    position: absolute;
    left: 582px;
    top: 130px;
    width: 416px;
    height: 470px;
    border-radius: 208px 208px 0 0;
    background: linear-gradient(180deg, var(--brand-teal), var(--brand-dark));
  }
  .person {
    position: absolute;
    left: 582px;
    width: 416px;
    top: 460px;
    text-align: center;
    color: var(--name-cream);
  }
  .person-name { font-size: 36px; font-weight: 500; }
  .person-role { font-size: 21px; font-style: italic; margin-top: 4px; }
</style>
</head>
<body>
  <div class="business-card">
    <div class="brand-name">BrightNestMums</div>
    <div class="strapline">Tap<span class="divider">|</span>Gather<span class="divider">|</span>Sorted</div>

    <div class="address">47 Kowhai Terrace, Ellerslie,<br>Auckland 1051, New Zealand</div>

    <ul class="contact-list">
      <li>
        <svg viewBox="0 0 20 20" aria-hidden="true"><rect x="5" y="1" width="10" height="18" rx="2"/><rect x="7" y="3.5" width="6" height="11" fill="#eceeec"/></svg>
        021 483 517
      </li>
      <li>
        <svg viewBox="0 0 20 20" aria-hidden="true"><path d="M3 8c0-3 3-5 7-5s7 2 7 5h-4V6H7v2z"/><rect x="3" y="10" width="14" height="8" rx="2"/></svg>
        +64 (0)9 571 4860
      </li>
      <li>
        <svg viewBox="0 0 20 20" aria-hidden="true"><rect x="1" y="4" width="18" height="12" rx="1"/><path d="M2 5l8 6 8-6" stroke="#eceeec" stroke-width="1.6" fill="none"/></svg>
        www.BrightNestMums.example
      </li>
      <li>
        <svg viewBox="0 0 20 20" aria-hidden="true"><circle cx="10" cy="10" r="8.5"/><path d="M1.5 10h17M10 1.5v17M4 5h12M4 15h12" stroke="#eceeec" stroke-width="1.2" fill="none"/></svg>
        lenaforbisher@brightnestmums.example
      </li>
    </ul>

    <div class="brand-graphic" role="img" aria-label="Large brand symbol in teal tones"></div>
    <div class="person">
      <div class="person-name">Lena Forbisher</div>
      <div class="person-role">Founder</div>
    </div>
  </div>
</body>
</html>
```